Create a wordpress website for Tovarin business solution

This project is to create a complete website with all pages.

Overview
The purpose of this project is to create a full complete website with all pages (16 pages). The site should be professional and modern. The site is for an IT recruiting and IT training company. The site needs to be easy to administer and update content. It should be simple to add pages, videos and testimonials later. I will leave the site layout, color schemes and flow to the designers.

Navigation Menu (Home, who we are, what we do, what makes us different, why it matters, candidate portal, contact us, Blog)

WHO WE ARE should be a drop down menu with link to pages (about us, mission, vision and purpose, our team)

WHAT WE DO should be drop down menu with link to the following pages (IT Recruiting, IT Training, Hardware and software sales)

What makes us different should be single page with different paragraph titles. (We live what we do, we don't compromise quality, we share knowledge, staffing guarantee)

Why it matters should be single page with paragraph titles. (Quickly fill positions, candidate career development)

Candidate portal should links to my portal login page. I can add the correct URL later. I just need it to link to somewhere. I can change it.

Contact us should have (address, phone number, google map and a form to submit request for a call back)

Blog - This link should launch a wordpress blogging module

Target Market(s)

IT RECRUITING AND CONSULTING

Industry/Entity Type

It Company

Coding

Coded - Design and coding required

Requirements
Must have
• Company Logo
• Navigation Menu (Home, who we are, what we do, what makes us different, why it matters, candidate portal, contact us)
• WHO WE ARE should be a drop down menu with link to pages (about us, mission, vision and purpose, our team)
• WHAT WE DO should be drop down menu with link to the following pages (IT Recruiting, IT Training, Hardware and software sales)
• What makes us different should be single page with different paragraph titles. (We live what we do, we don't compromise quality, we share knowledge, staffing guarantee)
• Why it matters should be single page with paragraph titles. (Quickly fill positions, candidate career development)
• Candidate portal should links to my portal login page. I can add the correct URL later. I just need it to link to somewhere. I can change it.
• Contact us should have (address, phone number, google map and a form to submit request for a call back)

```html
<!DOCTYPE html>
<html lang="en">
<head>
<meta charset="utf-8">
<title>Tovarin Business Solution LLC</title>
<link href="https://fonts.googleapis.com/css2?family=Lato:wght@400;700;900&family=Open+Sans:wght@400;600;700&family=Raleway:wght@400;500;600&display=swap" rel="stylesheet">
<style>
:root{
  --blue:#1b5a94;
  --blue-dark:#154a7c;
  --orange:#e8923a;
  --orange-soft:#efa24f;
  --orange-deep:#a5570f;
  --brown:#8a5a2a;
  --ink:#222;
  --text:#555;
  --muted:#888;
  --line:#d8d8d8;
  --white:#fff;
}
*{box-sizing:border-box;margin:0;padding:0}
html,body{width:1200px;height:3249px;overflow:hidden;background:var(--white)}
body{font-family:"Open Sans",Arial,sans-serif;color:var(--text);position:relative}
section,header,footer,nav{position:absolute;left:0;width:1200px}
.abs{position:absolute}

/* header */
.site-header{top:0;height:97px;background:var(--white);border-top:4px solid var(--blue)}
.brand{left:78px;top:8px;font-family:"Open Sans",sans-serif;font-weight:700;font-size:58px;color:var(--blue);letter-spacing:-1px;line-height:1}
.header-mail{left:625px;top:10px;font-size:16px;color:var(--ink);display:flex;align-items:center;gap:10px}
.header-phone{left:914px;top:0;width:238px;height:46px;background:var(--blue);color:var(--white);font-size:20px;display:flex;align-items:center;justify-content:center;gap:14px;border-radius:0 0 4px 4px}
.header-login{left:1072px;top:62px;font-size:17px;color:var(--blue);display:flex;align-items:center;gap:8px}

/* hero */
.hero{top:97px;height:629px}
.hero-photo{position:absolute;inset:0;background:linear-gradient(100deg,#c9b9a4 0%,#b4a38c 30%,#d6c7b2 55%,#8fa9c4 72%,#c7b59c 100%)}
.hero-title{left:80px;top:210px;font-family:"Lato",sans-serif;font-weight:900;font-size:62px;color:var(--orange);letter-spacing:0.5px}
.hero-text{left:80px;top:292px;width:560px;font-size:21px;line-height:26px;color:#111}
.btn{display:flex;align-items:center;justify-content:center;font-family:"Open Sans",sans-serif;border-radius:4px}
.btn-blue{background:var(--blue);color:var(--white)}
.hero-btn{left:78px;top:390px;width:186px;height:50px;font-size:20px}

/* nav */
.main-nav{top:726px;height:50px;background:#dc9d55;display:flex;align-items:center;padding-left:91px;font-size:17px;color:var(--ink)}
.main-nav span{padding:0 22px;height:50px;display:flex;align-items:center}
.main-nav .active{background:var(--orange-deep);color:var(--white);width:124px;justify-content:center;margin-right:8px}

/* welcome */
.welcome{top:776px;height:463px}
.section-title{width:1200px;text-align:center;font-family:"Raleway",sans-serif;font-weight:500;font-size:41px;color:var(--blue)}
.section-title em{font-style:normal;color:var(--orange-deep)}
.welcome .section-title{top:46px}
.tabs{left:353px;top:119px;width:492px;height:48px;display:flex;border:1px solid var(--line);border-top:none}
.tab{flex:1;display:flex;align-items:center;justify-content:center;gap:10px;font-size:18px;color:var(--ink);border-right:1px solid var(--line);border-top:1px solid var(--line)}
.tab:last-child{border-right:none}
.tab.active{border-top:3px solid var(--orange-deep)}
.mission-title{left:80px;top:204px;font-size:21px;font-weight:700;color:var(--ink)}
.mission-text{left:80px;top:238px;width:590px;font-size:16px;line-height:24px;color:#444}
.mission-text p+p{margin-top:20px}
.mission-btn{left:78px;top:366px;width:154px;height:44px;font-size:19px}
.mission-photo{left:706px;top:192px;width:418px;height:213px;border:2px solid #222;background:linear-gradient(120deg,#6d5040,#b9a58f 45%,#4a5f7a 75%,#c8b49a)}

/* what we do */
.services{top:1239px;height:472px;overflow:hidden}
.band-photo{position:absolute;inset:0;background:linear-gradient(90deg,#e9a45a,#f0b26b 40%,#eba35a 70%,#e69a4c)}
.services .section-title{top:48px;color:#111}
.service{top:120px;width:330px;text-align:center}
.service-icon{margin:0 auto;width:112px;height:112px;border-radius:50%;border:3px solid #fff3e2;display:flex;align-items:center;justify-content:center}
.service-icon .inner{width:96px;height:96px;border-radius:50%;display:flex;align-items:center;justify-content:center}
.stem{margin:0 auto;width:2px;height:30px;background:#4a3520}
.dot{margin:0 auto;width:20px;height:20px;border-radius:50%;border:2px solid #4a3520}
.service h3{margin-top:24px;font-family:"Open Sans",sans-serif;font-weight:400;font-size:21px;color:#111;line-height:26px}
.service p{margin-top:6px;font-size:15px;line-height:22px;color:#2a2a2a}

/* testimonials */
.testimonials{top:1711px;height:282px}
.testimonials .section-title{top:44px}
.tm-arrow{top:142px;color:var(--orange);font-size:30px}
.tm-quote{left:225px;top:134px;width:59px;height:65px;border:2px solid var(--orange);background:var(--orange-soft);display:flex;align-items:center;justify-content:center}
.tm-photo{left:284px;top:115px;width:106px;height:102px;border:2px solid #333;background:linear-gradient(160deg,#f2f2f2,#d8c7b8 55%,#efe8e2)}
.tm-text{left:422px;top:117px;width:560px;font-size:15px;line-height:21px;color:#444}
.tm-name{left:422px;top:183px;font-size:15px;color:var(--orange-deep)}
.tm-role{left:428px;top:207px;font-size:15px;color:var(--muted)}
.tm-stars{left:862px;top:208px;display:flex;gap:2px}

/* careers */
.careers{top:1993px;height:314px}
.careers .band-photo{background:linear-gradient(180deg,#ee9c4c,#f0a55c 50%,#e8974a)}
.careers-title{top:62px;width:1200px;text-align:center;font-family:"Raleway",sans-serif;font-weight:400;font-size:52px;color:#111}
.careers-text{left:150px;top:137px;width:900px;text-align:center;font-size:17px;line-height:30px;color:#222}
.careers-text b{font-weight:400;font-size:22px}
.careers-btn{left:522px;top:223px;width:156px;height:47px;background:var(--white);color:#222;font-size:17px;box-shadow:0 1px 3px rgba(0,0,0,.2)}

/* blogs */
.blogs{top:2307px;height:526px}
.blogs .section-title{top:45px}
.post{top:123px;width:314px}
.post-photo{height:158px}
.post-date{margin-top:14px;font-size:12px;color:var(--muted);display:flex;align-items:center;gap:8px}
.post h4{margin-top:10px;font-size:16px;font-weight:400;color:#333}
.post:first-of-type h4{color:var(--blue)}
.post p{margin-top:8px;font-size:15px;line-height:21px;color:#555}
.post-author{margin-top:14px;font-size:14px;color:#555;display:flex;align-items:center;gap:10px}
.post-author b{font-weight:400;color:var(--blue)}
.avatar{width:34px;height:34px;border-radius:50%;background:#d5d5d5}

/* footer */
.site-footer{top:2833px;height:366px;background:var(--orange)}
.foot-brand{left:78px;top:112px;font-weight:700;font-size:42px;color:var(--white);line-height:1}
.foot-about{left:78px;top:178px;width:270px;font-size:15px;line-height:21px;color:var(--white)}
.socials{left:78px;top:260px;display:flex;gap:13px}
.socials span{width:44px;height:44px;border:1px solid var(--white);border-radius:3px;background:rgba(255,255,255,.12)}
.socials span:first-child{background:var(--white)}
.foot-head{top:52px;font-size:21px;color:var(--white);padding-bottom:8px;border-bottom:1px solid rgba(255,255,255,.6);width:190px}
.quick-links{left:373px;top:118px;list-style:none;font-size:15px;color:var(--white);line-height:31px}
.quick-links li::before{content:"›";margin-right:10px}
.contact-item{left:609px;font-size:14px;color:var(--white);display:flex;gap:12px;line-height:22px}
.foot-map{left:873px;top:108px;width:247px;height:178px;border:2px solid #333;background:linear-gradient(135deg,#e4e2da,#d3d9c8 50%,#e7e4dc)}

.copyright{left:0;top:3199px;width:1200px;height:50px;display:flex;align-items:center;justify-content:center;font-size:15px;color:#333}
.copyright b{color:var(--orange-deep);margin:0 6px}
</style>
</head>
<body>

<header class="site-header">
  <div class="abs brand">tovarin</div>
  <div class="abs header-mail">
    <svg width="22" height="16" viewBox="0 0 22 16"><rect x="1" y="1" width="20" height="14" fill="none" stroke="#e8923a" stroke-width="2"/><path d="M1 1 L11 9 L21 1" fill="none" stroke="#e8923a" stroke-width="2"/></svg>
    hello@tovarinmail.com
  </div>
  <div class="abs header-phone">
    <svg width="20" height="20" viewBox="0 0 24 24"><path d="M6 2 L9 2 L11 7 L8 9 Q10 14 15 16 L17 13 L22 15 L22 18 Q22 22 18 22 Q3 20 2 6 Q2 2 6 2Z" fill="none" stroke="#fff" stroke-width="2"/></svg>
    555 014 2876
  </div>
  <div class="abs header-login">
    <svg width="16" height="16" viewBox="0 0 16 16"><rect x="2" y="7" width="12" height="8" fill="#e8923a"/><path d="M5 7 V4 a3 3 0 0 1 6 0 V7" fill="none" stroke="#e8923a" stroke-width="2"/></svg>
    Login
  </div>
</header>

<section class="hero">
  <div class="hero-photo" role="img" aria-label="Smiling young professional holding a tablet in a bright office"></div>
  <h1 class="abs hero-title">LOOKING FOR A JOB?</h1>
  <p class="abs hero-text">Lorem Ipsum is simply dummy text of the printing and typesetting industry. Lorem Ipsum has been the industry's standard dummy text ever since the 1500.</p>
  <a class="abs btn btn-blue hero-btn">JOIN US NOW</a>
</section>

<nav class="main-nav">
  <span class="active">Home</span>
  <span>About</span>
  <span>Service</span>
  <span>What makes us different</span>
  <span>Why it matters</span>
  <span>Candidate Portal</span>
  <span>Contact</span>
</nav>

<section class="welcome">
  <h2 class="abs section-title">Welcome To <em>Tovarin Business Solution LLC</em></h2>
  <div class="abs tabs">
    <div class="tab active"><svg width="16" height="16" viewBox="0 0 16 16"><path d="M15 1 L1 7 L8 8 L9 15Z" fill="#a5570f"/></svg>Our Mission</div>
    <div class="tab"><svg width="20" height="14" viewBox="0 0 20 14"><path d="M1 7 Q10 -3 19 7 Q10 17 1 7Z" fill="#222"/><circle cx="10" cy="7" r="3" fill="#fff"/></svg>Our Vision</div>
    <div class="tab"><svg width="18" height="16" viewBox="0 0 18 16"><path d="M1 1 V15 H17" fill="none" stroke="#222" stroke-width="2"/><path d="M4 11 L8 6 L11 9 L16 3" fill="none" stroke="#222" stroke-width="2"/></svg>Our History</div>
  </div>
  <h3 class="abs mission-title">We Have Great Mission</h3>
  <div class="abs mission-text">
    <p>Lorem ipsum dolor sit amet, consectetur adipisicing elit, sed do eiusmod tempor incididunt ut labore et dolore magna aliqua.</p>
    <p>ullamco laboris nisi ut aliquip ex ea commodo consequat. Duis aute irure dolor in reprehenderit.</p>
  </div>
  <a class="abs btn btn-blue mission-btn">READ MORE</a>
  <div class="abs mission-photo" role="img" aria-label="Group of students working together at laptops"></div>
</section>

<section class="services">
  <div class="band-photo" role="img" aria-label="Blurred classroom scene under a warm orange tint"></div>
  <h2 class="abs section-title">What We Do?</h2>

  <div class="abs service" style="left:69px">
    <div class="service-icon"><div class="inner" style="background:#e9a14f">
      <svg width="48" height="48" viewBox="0 0 48 48"><circle cx="24" cy="14" r="6" fill="#222"/><circle cx="11" cy="20" r="5" fill="#222"/><circle cx="37" cy="20" r="5" fill="#222"/><path d="M14 38 Q14 24 24 24 Q34 24 34 38Z" fill="#222"/><path d="M3 38 Q3 28 11 28 Q15 28 16 30 L14 38Z M45 38 Q45 28 37 28 Q33 28 32 30 L34 38Z" fill="#222"/></svg>
    </div></div>
    <div class="stem"></div><div class="dot"></div>
    <h3>IT Recuiting</h3>
    <p>Lorem Ipsum is simply dummy text of the printing and typesetting industry.</p>
  </div>

  <div class="abs service" style="left:435px">
    <div class="service-icon"><div class="inner" style="background:#d97b2a">
      <svg width="48" height="48" viewBox="0 0 48 48"><rect x="6" y="8" width="36" height="24" fill="none" stroke="#fff" stroke-width="3"/><path d="M18 40 H30 M24 32 V40" stroke="#fff" stroke-width="3"/><circle cx="24" cy="20" r="5" fill="#fff"/></svg>
    </div></div>
    <div class="stem"></div><div class="dot"></div>
    <h3>IT Training</h3>
    <p>Lorem Ipsum is simply dummy text of the printing and typesetting industry.</p>
  </div>

  <div class="abs service" style="left:799px">
    <div class="service-icon"><div class="inner" style="background:#9a5f22">
      <svg width="48" height="48" viewBox="0 0 48 48"><rect x="6" y="24" width="16" height="14" fill="#f3d2a8"/><rect x="26" y="24" width="16" height="14" fill="#f3d2a8"/><rect x="16" y="8" width="16" height="14" fill="#f3d2a8"/></svg>
    </div></div>
    <div class="stem"></div><div class="dot"></div>
    <h3>Hardware and Software<br>Sales</h3>
    <p>Lorem Ipsum is simply dummy text of the printing and typesetting industry.</p>
  </div>
</section>

<section class="testimonials">
  <h2 class="abs section-title">What Our <em>Customer Say</em></h2>
  <div class="abs tm-arrow" style="left:138px">‹</div>
  <div class="abs tm-arrow" style="left:1055px">›</div>
  <div class="abs tm-quote"><svg width="30" height="24" viewBox="0 0 30 24"><path d="M2 22 V12 Q2 3 12 2 V6 Q7 7 7 12 H12 V22Z M17 22 V12 Q17 3 27 2 V6 Q22 7 22 12 H27 V22Z" fill="#d47d28"/></svg></div>
  <div class="abs tm-photo" role="img" aria-label="Portrait of a smiling businesswoman"></div>
  <p class="abs tm-text">"Lorem Ipsum is simply dummy text of the printing and typesetting industry. Lorem Ipsum has been the industry's standard dummy text ever since the 1500s."</p>
  <div class="abs tm-name">- Clara Weston</div>
  <div class="abs tm-role">Senior Vice President</div>
  <div class="abs tm-stars">
    <svg width="114" height="22" viewBox="0 0 114 22" fill="#1b6fc9">
      <path id="s" d="M11 1 L14 8 L21 8 L15.5 12.5 L17.5 20 L11 15.5 L4.5 20 L6.5 12.5 L1 8 L8 8Z"/>
      <use href="#s" x="23"/><use href="#s" x="46"/><use href="#s" x="69"/>
      <path d="M103 1 L100 8 L93 8 L98.5 12.5 L96.5 20 L103 15.5Z"/>
    </svg>
  </div>
</section>

<section class="careers">
  <div class="band-photo" role="img" aria-label="Crowd of job seekers under a warm orange tint"></div>
  <h2 class="abs careers-title">Careers</h2>
  <p class="abs careers-text">We are looking for capable individuals to join our company for the training &amp; Placement. If you have what it takes to excel, please drop us an email with your resume to &nbsp;<b>hello@tovarinmail.com</b></p>
  <a class="abs btn careers-btn">LOGIN NOW</a>
</section>

<section class="blogs">
  <h2 class="abs section-title">Recent Blogs</h2>

  <article class="abs post" style="left:78px">
    <div class="post-photo" role="img" aria-label="Team of business people standing together" style="background:linear-gradient(120deg,#4d4f58,#b9b3ad 50%,#3f4148)"></div>
    <div class="post-date"><svg width="14" height="14" viewBox="0 0 14 14"><rect x="1" y="2" width="12" height="11" fill="none" stroke="#aaa" stroke-width="1.5"/><path d="M1 5 H13" stroke="#aaa" stroke-width="1.5"/></svg>30,Nov 2016</div>
    <h4>Lorem Ipsum is simply dummy text...</h4>
    <p>Lorem Ipsum is simply dummy text of the printing and typesetting industry. Lorem Ipsum has been the industry...</p>
    <div class="post-author"><span class="avatar"></span>By <b>ADMIN</b></div>
  </article>

  <article class="abs post" style="left:444px">
    <div class="post-photo" role="img" aria-label="Business meeting in a bright white lounge" style="background:linear-gradient(120deg,#eef0f2,#c9ccd1 50%,#f4f4f4)"></div>
    <div class="post-date"><svg width="14" height="14" viewBox="0 0 14 14"><rect x="1" y="2" width="12" height="11" fill="none" stroke="#aaa" stroke-width="1.5"/><path d="M1 5 H13" stroke="#aaa" stroke-width="1.5"/></svg>30,Nov 2016</div>
    <h4>Lorem Ipsum is simply dummy text...</h4>
    <p>Lorem Ipsum is simply dummy text of the printing and typesetting industry. Lorem Ipsum has been the industry...</p>
    <div class="post-author"><span class="avatar"></span>By <b>ADMIN</b></div>
  </article>

  <article class="abs post" style="left:810px">
    <div class="post-photo" role="img" aria-label="Colleagues discussing work at an office desk" style="background:linear-gradient(120deg,#c9c6bf,#6e5a48 50%,#d9d4cb)"></div>
    <div class="post-date"><svg width="14" height="14" viewBox="0 0 14 14"><rect x="1" y="2" width="12" height="11" fill="none" stroke="#aaa" stroke-width="1.5"/><path d="M1 5 H13" stroke="#aaa" stroke-width="1.5"/></svg>30,Nov 2016</div>
    <h4>Lorem Ipsum is simply dummy text...</h4>
    <p>Lorem Ipsum is simply dummy text of the printing and typesetting industry. Lorem Ipsum has been the industry...</p>
    <div class="post-author"><span class="avatar"></span>By <b>ADMIN</b></div>
  </article>
</section>

<footer class="site-footer">
  <div class="abs foot-brand">tovarin</div>
  <p class="abs foot-about">Lorem Ipsum is simply dummy text of the printing and typesetting industry.</p>
  <div class="abs socials"><span></span><span></span><span></span><span></span></div>

  <div class="abs foot-head" style="left:373px">Quick Links</div>
  <ul class="abs quick-links">
    <li>Home</li><li>Who we are</li><li>What we Do</li><li>What makes us different</li><li>Why it Matter</li><li>Candidate Portal</li><li>Contact Us</li>
  </ul>

  <div class="abs foot-head" style="left:609px">Contact Us</div>
  <div class="abs contact-item" style="top:118px">
    <svg width="16" height="20" viewBox="0 0 16 20"><path d="M8 19 Q1 10 1 7 a7 7 0 0 1 14 0 Q15 10 8 19Z" fill="none" stroke="#fff" stroke-width="1.6"/><circle cx="8" cy="7" r="2.5" fill="#fff"/></svg>
    <span>Tovarin business solution llc.<br>123,Lorem Ipsum,<br>Country,123456</span>
  </div>
  <div class="abs contact-item" style="top:212px">
    <svg width="18" height="18" viewBox="0 0 24 24"><path d="M6 2 L9 2 L11 7 L8 9 Q10 14 15 16 L17 13 L22 15 L22 18 Q22 22 18 22 Q3 20 2 6 Q2 2 6 2Z" fill="none" stroke="#fff" stroke-width="2"/></svg>
    <span>555 014 2876</span>
  </div>
  <div class="abs contact-item" style="top:256px">
    <svg width="20" height="16" viewBox="0 0 22 16"><rect x="1" y="1" width="20" height="14" fill="none" stroke="#fff" stroke-width="1.6"/><path d="M1 1 L11 9 L21 1" fill="none" stroke="#fff" stroke-width="1.6"/></svg>
    <span>hello@tovarinmail.com</span>
  </div>
  <div class="abs foot-map" role="img" aria-label="Street map showing the office location"></div>
</footer>

<div class="abs copyright">© <b>Tovarin business solution llc</b> - 2016 All Right Reserved</div>

</body>
</html>
```